Professional and Fun Business Cards for #1 Lagoon Care

We want an updated look for our existing business cards. In addition, we need to update the logos on the back side of the card to be the most current award for Tovey's Index. I have an eps of the Tovey's Index award logo but it is too big to upload here, so I can email it to the designer once selected.

Target Market(s)

Families with swimming pools

Industry/Entity Type

Business

Contact Information for Business Card

Martin Dobrev
Partner & Senior Pool Technician
Dobrev & Kin Pool Service, Inc.
2480 Larkhaven Drive, Suite 312
Roseville, CA 95874
(916) 555-0143 service
(916) 555-0187 billing
info@dobrev-kin.example
www.dobrev-kin.example

Font styles to use
Other font styles liked:
• Goudy Sans Bold

Colors
3176b5
34a7d8
34b8a4
add136

Requirements
Must have
• Dobrev & Kin logo and contact information on the front
• All other logos on the back
Nice to have
• Open to ideas...
Should not have
• Can't think of anything specific

```html
<!DOCTYPE html>
<html lang="en">
<head>
<meta charset="utf-8">
<title>Dobrev &amp; Kin Pool Service – Business Cards</title>
<link rel="stylesheet" href="https://fonts.googleapis.com/css2?family=Alegreya+Sans:wght@400;500;700&display=swap">
<style>
  :root {
    --bg: #e9ecee;
    --card: #ffffff;
    --card-shade: #f1f3f4;
    --teal: #3fc6bb;
    --teal-dark: #2aa69c;
    --teal-text: #34b8a4;
    --blue: #3176b5;
    --ink: #1d1f22;
    --muted: #44484d;
    --band: #111315;
  }
  * { margin: 0; padding: 0; box-sizing: border-box; }
  html, body { width: 1200px; height: 885px; overflow: hidden; }
  body {
    background: var(--bg);
    font-family: "Alegreya Sans", "Trebuchet MS", sans-serif;
    position: relative;
  }
  .card {
    position: absolute;
    width: 560px;
    height: 320px;
    background: linear-gradient(135deg, var(--card) 0%, var(--card-shade) 100%);
    border-radius: 4px;
    box-shadow: 0 10px 28px rgba(0,0,0,.18);
    overflow: hidden;
  }
  .card--front { left: 30px; top: 130px; }
  .card--back { left: 610px; top: 435px; }

  .front-wave { position: absolute; inset: 0; }

  .front-details {
    position: absolute;
    top: 18px;
    right: 26px;
    text-align: right;
    color: var(--ink);
    white-space: nowrap;
  }
  .company-name {
    color: var(--teal-text);
    font-size: 22px;
    font-weight: 500;
    line-height: 26px;
  }
  .person-name { font-size: 19px; font-weight: 700; line-height: 22px; margin-top: 2px; }
  .person-title { font-size: 13px; color: var(--muted); line-height: 16px; }
  .contact-list { list-style: none; margin-top: 12px; font-size: 13.5px; line-height: 19px; }
  .contact-list li { display: flex; justify-content: flex-end; align-items: center; gap: 8px; }
  .contact-list svg { width: 12px; height: 12px; flex: none; }
  .contact-list .no-icon { padding-right: 20px; }

  .logo {
    position: absolute;
    display: flex;
    align-items: center;
    gap: 10px;
  }
  .logo-square { width: 30px; height: 30px; background: var(--blue); flex: none; }
  .logo-name {
    color: var(--blue);
    font-weight: 700;
    font-size: 26px;
    line-height: 30px;
    white-space: nowrap;
  }
  .logo--front { left: 34px; bottom: 18px; }
  .logo--back { left: 130px; top: 78px; }
  .logo--back .logo-square { width: 46px; height: 46px; }
  .logo--back .logo-name { font-size: 40px; line-height: 46px; }

  .badges {
    position: absolute;
    left: 26px;
    bottom: 24px;
    display: flex;
    gap: 14px;
  }
  .badge {
    width: 76px;
    height: 62px;
    border: 2px solid var(--teal);
    border-radius: 9px;
    background: #fff;
    display: grid;
    place-items: center;
  }
  .badge-seal { width: 42px; height: 42px; border-radius: 50%; }
  .badge--award .badge-seal { background: radial-gradient(circle, #e8d98a 0%, #c9b253 100%); }
  .badge--cert .badge-seal { background: radial-gradient(circle, #d6e0f2 0%, #7d94c9 100%); }
</style>
</head>
<body>

  <section class="card card--front" aria-label="Business card front">
    <svg class="front-wave" viewBox="0 0 560 320" width="560" height="320" aria-hidden="true">
      <defs>
        <linearGradient id="tealFill" x1="0" y1="0" x2="1" y2="1">
          <stop offset="0" stop-color="#6fdcd2"/>
          <stop offset="1" stop-color="#2aa69c"/>
        </linearGradient>
      </defs>
      <path d="M0 76 Q 170 326 560 288 L560 300 Q 170 340 0 90 Z" fill="var(--band)"/>
      <path d="M0 90 Q 170 340 560 300 L560 320 L0 320 Z" fill="url(#tealFill)"/>
    </svg>

    <div class="front-details">
      <div class="company-name">Dobrev &amp; Kin Pool Service, Inc.</div>
      <div class="person-name">Martin Dobrev</div>
      <div class="person-title">Partner &amp; Senior Pool Technician</div>
      <ul class="contact-list">
        <li>(916) 555-0143
          <svg viewBox="0 0 12 12"><path d="M2.5 1 L4.5 1 L5 3.5 L3.8 4.6 Q5 7 7.4 8.2 L8.5 7 L11 7.5 L11 9.5 Q11 11 9.5 11 Q1 10 1 2.5 Q1 1 2.5 1Z" fill="var(--teal)"/></svg></li>
        <li>(916) 555-0187
          <svg viewBox="0 0 12 12"><path d="M2.5 1 L4.5 1 L5 3.5 L3.8 4.6 Q5 7 7.4 8.2 L8.5 7 L11 7.5 L11 9.5 Q11 11 9.5 11 Q1 10 1 2.5 Q1 1 2.5 1Z" fill="var(--teal)"/></svg></li>
        <li>info@dobrev-kin.example
          <svg viewBox="0 0 12 12"><rect x="1" y="2.5" width="10" height="7" rx="1" fill="var(--teal)"/><path d="M1.5 3 L6 6.5 L10.5 3" stroke="#fff" fill="none"/></svg></li>
        <li>www.dobrev-kin.example
          <svg viewBox="0 0 12 12"><circle cx="6" cy="6" r="5" fill="none" stroke="var(--teal)" stroke-width="1.3"/><ellipse cx="6" cy="6" rx="2" ry="5" fill="none" stroke="var(--teal)"/><path d="M1 6 H11" stroke="var(--teal)"/></svg></li>
        <li>2480 Larkhaven Drive, Suite 312 Roseville
          <svg viewBox="0 0 12 12"><path d="M6 11 Q2 6.5 2 4.5 A4 4 0 0 1 10 4.5 Q10 6.5 6 11Z" fill="var(--teal)"/><circle cx="6" cy="4.5" r="1.5" fill="#fff"/></svg></li>
        <li class="no-icon">CA 95874</li>
      </ul>
    </div>

    <div class="logo logo--front">
      <span class="logo-square"></span>
      <span class="logo-name">Dobrev &amp; Kin</span>
    </div>
  </section>

  <section class="card card--back" aria-label="Business card back">
    <div class="logo logo--back">
      <span class="logo-square"></span>
      <span class="logo-name">Dobrev &amp; Kin</span>
    </div>

    <div class="badges">
      <div class="badge badge--award" role="img" aria-label="Listing award badge"><span class="badge-seal"></span></div>
      <div class="badge badge--cert" role="img" aria-label="Certified spa operator badge"><span class="badge-seal"></span></div>
    </div>
  </section>

</body>
</html>
```